Business card for law firm

Need business card for new law firm. Think confident, authoritative, conservative, but not stuffy or old-fashioned.

Contact Information for Business Card

Content for card - logo (uploaded), plus the following:

Paul Whitcombe (larger font)
Managing Partner (larger font, but not as large as name)
Level 9, 7 Ferris Lane
Sydney NSW 2000
Main Tel 02 9364 2710
Direct Tel 02 8472 3159
Email paul@qvlegal.com.au
www.qvlegal.com.au

Letterhead design should include logo plus:
Level 9, 7 Ferris Lane
Sydney NSW 2000
Tel 02 8472 3159
www.qvlegal.com.au

```html
<!DOCTYPE html>
<html lang="en">
<head>
<meta charset="utf-8">
<title>QV Legal – Business Card</title>
<link rel="stylesheet" href="https://fonts.googleapis.com/css2?family=Open+Sans:wght@400;700&display=swap">
<style>
  :root {
    --navy: #0c1f5c;
    --ink: #1b1b1b;
    --black: #050505;
    --white: #ffffff;
    --divider: #9a9a9a;
    --bg-light: #ececec;
    --bg-dark: #c8c9cb;
  }
  * { margin: 0; padding: 0; box-sizing: border-box; }
  html, body { width: 1200px; height: 1113px; overflow: hidden; }
  body {
    position: relative;
    font-family: "Open Sans", Arial, sans-serif;
    background: linear-gradient(135deg, var(--bg-light) 0%, var(--bg-dark) 100%);
  }
  .card {
    position: absolute;
    width: 767px;
    height: 440px;
    border-radius: 40px;
    overflow: hidden;
  }
  .card--front { left: 70px; top: 100px; background: var(--white); box-shadow: 0 0 0 1px #cfcfcf; }
  .card--back { left: 345px; top: 595px; background: var(--black); }

  .front-brand {
    position: absolute; left: 84px; top: 100px; width: 320px;
    display: flex; flex-direction: column; align-items: center;
  }
  .brand-mark { width: 72px; height: 72px; background: var(--navy); }
  .brand-name {
    margin-top: 44px; font-size: 46px; font-weight: 400; letter-spacing: 3px;
    color: var(--black); line-height: 1; white-space: nowrap;
  }
  .divider {
    position: absolute; left: 423px; top: 70px; width: 2px; height: 263px; background: var(--divider);
  }
  .contact { position: absolute; left: 445px; top: 66px; color: var(--ink); }
  .contact__name { font-size: 27px; font-weight: 700; color: var(--navy); line-height: 1.2; }
  .contact__role { font-size: 20px; line-height: 1.4; margin-bottom: 8px; }
  .contact__address { font-size: 20px; line-height: 31px; margin-bottom: 8px; }
  .contact__list { list-style: none; font-size: 20px; }
  .contact__list li { display: flex; align-items: center; gap: 7px; height: 33px; }
  .contact__list svg { width: 17px; height: 17px; flex: none; }

  .front-waves { position: absolute; left: 0; top: 0; width: 767px; height: 440px; }

  .back-brand {
    position: absolute; left: 0; top: 80px; width: 100%;
    display: flex; flex-direction: column; align-items: center;
  }
  .card--back .brand-mark { width: 90px; height: 90px; background: var(--white); }
  .card--back .brand-name { margin-top: 64px; font-size: 58px; color: var(--white); }
  .back-url {
    position: absolute; left: 0; top: 384px; width: 100%; text-align: center;
    color: var(--white); font-size: 24px; letter-spacing: 4px;
  }
  .back-url strong { font-weight: 700; }
</style>
</head>
<body>

<section class="card card--front">
  <div class="front-brand">
    <div class="brand-mark"></div>
    <div class="brand-name">QV LEGAL</div>
  </div>

  <div class="divider"></div>

  <div class="contact">
    <div class="contact__name">PAUL WHITCOMBE</div>
    <div class="contact__role">MANAGING PARTNER</div>
    <div class="contact__address">Level 9, 7 Ferris Lane<br>Sydney NSW 2000</div>
    <ul class="contact__list">
      <li>
        <svg viewBox="0 0 16 16"><circle cx="8" cy="8" r="7" fill="none" stroke="var(--navy)" stroke-width="1.5"/><path d="M6 4.5c-1 1-1 3.5.5 5.5s3.5 2.5 4 1.5l-1.2-1.2-1 .6c-.8-.5-1.7-1.7-1.9-2.6l.9-.7z" fill="var(--navy)"/></svg>
        02 9364 2710(Main)
      </li>
      <li>
        <svg viewBox="0 0 16 16"><circle cx="8" cy="8" r="7" fill="none" stroke="var(--navy)" stroke-width="1.5"/><path d="M6 4.5c-1 1-1 3.5.5 5.5s3.5 2.5 4 1.5l-1.2-1.2-1 .6c-.8-.5-1.7-1.7-1.9-2.6l.9-.7z" fill="var(--navy)"/></svg>
        02 8472 3159(Direct)
      </li>
      <li>
        <svg viewBox="0 0 16 16"><path d="M1 6.5 8 2l7 4.5V14H1z" fill="var(--navy)"/><path d="M2.5 7 8 10.5 13.5 7" fill="none" stroke="var(--white)" stroke-width="1.2"/></svg>
        paul@qvlegal.com.au
      </li>
      <li>
        <svg viewBox="0 0 16 16" fill="none" stroke="var(--navy)" stroke-width="1.2"><circle cx="8" cy="8" r="6.5"/><ellipse cx="8" cy="8" rx="3" ry="6.5"/><path d="M1.5 8h13M2.5 4.8h11M2.5 11.2h11"/></svg>
        www.qvlegal.com.au
      </li>
    </ul>
  </div>

  <svg class="front-waves" viewBox="0 0 767 440" aria-hidden="true">
    <path d="M0 400 C120 378 240 382 400 398 C560 414 680 398 767 354 L767 392 C680 428 560 432 400 424 C250 416 120 416 0 430 Z" fill="var(--black)"/>
    <path d="M0 440 L0 438 C150 418 320 424 520 438 C650 446 720 432 767 404 L767 440 Z" fill="var(--navy)"/>
    <path d="M10 430 C150 412 320 418 530 434" fill="none" stroke="var(--white)" stroke-width="3"/>
    <path d="M255 378 C380 396 470 410 590 418" fill="none" stroke="var(--white)" stroke-width="2"/>
  </svg>
</section>

<section class="card card--back">
  <div class="back-brand">
    <div class="brand-mark"></div>
    <div class="brand-name">QV LEGAL</div>
  </div>
  <div class="back-url">www.<strong>qvlegal</strong>.com.au</div>
</section>

</body>
</html>
```